Oil Field Service company needs professional business cards

Looking to clean up our current company business cards and look a little more professional. Brenwick Casing Services is a US based company that services the oil field. We deal with engineers, managers and oil rigs....................................................................................................................................................................................................................................................................................................................................................................................................

Target Market(s)

Oil and Gas professionals

Industry/Entity Type

Oil And Gas

Contact Information for Business Card

See attached photo as example

Font styles to use
Sans Serif

Colors
ec1f27

Requirements
Must have
• Company Logo, Name, Title, Cell, Office, Fax, Email.
• See attached photo
Nice to have
• External CRT, Internal CRT, Casing Crews, Torque Turn, Laydown Machine
Should not have
• Do not introduce any new pictures and keep it professional looking

```html
<!DOCTYPE html>
<html lang="en">
<head>
<meta charset="utf-8">
<title>Brenwick Casing Services – Business Card</title>
<link href="https://fonts.googleapis.com/css2?family=Source+Sans+3:wght@400;600;700&display=swap" rel="stylesheet">
<style>
  :root {
    --brand-red: #ec1f27;
    --slate: #45545f;
    --ink: #4b5158;
    --paper: #fbfbfb;
    --backdrop: #e9eaeb;
    --white: #ffffff;
  }
  * { box-sizing: border-box; margin: 0; padding: 0; }
  html, body {
    width: 1105px; height: 1200px; overflow: hidden;
    background: var(--backdrop);
    font-family: "Source Sans 3", Arial, sans-serif;
  }
  .card {
    position: absolute; left: 192px;
    width: 720px; height: 411px;
    overflow: hidden;
  }
  .card--front { top: 166px; background: var(--paper); }
  .card--back { top: 622px; background: var(--slate); }

  .wordmark {
    position: absolute;
    display: flex; align-items: center; gap: 12px;
    font-weight: 700; font-size: 29px; line-height: 1.1;
    letter-spacing: 0.5px; text-transform: uppercase;
  }
  .wordmark__square { width: 16px; height: 16px; flex: none; }
  .card--front .wordmark { left: 58px; top: 118px; color: var(--slate); }
  .card--front .wordmark__square { background: var(--brand-red); }
  .card--back .wordmark { left: 60px; top: 180px; color: var(--white); }
  .card--back .wordmark__square { background: var(--white); }

  .divider { position: absolute; width: 1px; }
  .card--front .divider { left: 392px; top: 81px; height: 249px; background: #d6d8da; }
  .card--back .divider { left: 402px; top: 120px; height: 182px; background: #c9ced2; }

  .contact { position: absolute; left: 425px; top: 84px; color: var(--ink); }
  .contact__name { color: var(--brand-red); font-weight: 600; font-size: 27px; line-height: 1; }
  .contact__title { font-size: 20px; margin-top: 8px; line-height: 1; }
  .contact__address { font-size: 19px; margin-top: 15px; line-height: 1; }
  .contact__list { list-style: none; margin-top: 17px; }
  .contact__item {
    display: flex; align-items: center; gap: 11px;
    font-size: 19px; height: 27.6px;
  }
  .contact__icon { width: 18px; height: 18px; fill: var(--brand-red); flex: none; }

  .accent-line { position: absolute; left: 0; top: 378px; width: 100%; height: 3px; background: var(--brand-red); }
  .accent-band { position: absolute; left: 0; top: 387px; width: 100%; height: 24px; background: var(--slate); }

  .services {
    position: absolute; left: 439px; top: 132px;
    list-style: none; color: var(--white); font-size: 20px;
  }
  .services__item { height: 30.4px; display: flex; align-items: center; gap: 9px; }
  .services__item::before {
    content: ""; width: 8px; height: 8px; border-radius: 50%; background: var(--white);
  }
</style>
</head>
<body>
  <section class="card card--front" aria-label="Business card front">
    <div class="wordmark"><span class="wordmark__square"></span><span>Brenwick<br>Casing Services</span></div>
    <div class="divider"></div>
    <div class="contact">
      <p class="contact__name">Cody Harlan</p>
      <p class="contact__title">Area Manager</p>
      <p class="contact__address">Ridgeton, OK 73950</p>
      <ul class="contact__list">
        <li class="contact__item">
          <svg class="contact__icon" viewBox="0 0 24 24" aria-label="Office"><path d="M6.6 10.8a15 15 0 0 0 6.6 6.6l2.2-2.2c.3-.3.7-.4 1-.2 1.1.4 2.3.6 3.6.6.6 0 1 .4 1 1V20c0 .6-.4 1-1 1A17 17 0 0 1 3 4c0-.6.4-1 1-1h3.5c.6 0 1 .4 1 1 0 1.3.2 2.5.6 3.6.1.3 0 .7-.2 1z"/></svg>
          (555)210-4800
        </li>
        <li class="contact__item">
          <svg class="contact__icon" viewBox="0 0 24 24" aria-label="Cell"><path d="M7 1h10a2 2 0 0 1 2 2v18a2 2 0 0 1-2 2H7a2 2 0 0 1-2-2V3a2 2 0 0 1 2-2zm0 3v14h10V4zm5 15.5a1.2 1.2 0 1 0 0 2.4 1.2 1.2 0 0 0 0-2.4z"/></svg>
          (555)318-6274
        </li>
        <li class="contact__item">
          <svg class="contact__icon" viewBox="0 0 24 24" aria-label="Fax"><path d="M6 2h12v6H6zM3 9h18a1 1 0 0 1 1 1v8h-4v4H6v-4H2v-8a1 1 0 0 1 1-1zm5 8v3h8v-3z"/></svg>
          (555)210-4830
        </li>
        <li class="contact__item">
          <svg class="contact__icon" viewBox="0 0 24 24" aria-label="Email"><path d="M2 5h20v14H2zm2 2v.5l8 5 8-5V7z"/></svg>
          cody@brenwick.com
        </li>
        <li class="contact__item">
          <svg class="contact__icon" viewBox="0 0 24 24" aria-label="Website"><path d="M12 2a10 10 0 1 0 0 20 10 10 0 0 0 0-20zm-1 17.9A8 8 0 0 1 4.1 10l4.9 5v1a2 2 0 0 0 2 2zm6.9-2.5A2 2 0 0 0 16 16h-1v-3a1 1 0 0 0-1-1H8v-2h2a1 1 0 0 0 1-1V7h2a2 2 0 0 0 2-2v-.4a8 8 0 0 1 2.9 12.8z"/></svg>
          www.brenwick.com
        </li>
      </ul>
    </div>
    <div class="accent-line"></div>
    <div class="accent-band"></div>
  </section>

  <section class="card card--back" aria-label="Business card back">
    <div class="wordmark"><span class="wordmark__square"></span><span>Brenwick<br>Casing Services</span></div>
    <div class="divider"></div>
    <ul class="services">
      <li class="services__item">External CRT</li>
      <li class="services__item">Internal CRT</li>
      <li class="services__item">Casing Crews</li>
      <li class="services__item">Torque Turn</li>
      <li class="services__item">Laydown Machine</li>
    </ul>
  </section>
</body>
</html>
```